MRT Property - Business Cards

Looking for a business card & general letterhead, signage etc design for our new logo.

Colours:
000a20
0056a2
00b5ef
0088ce
68cef2

Fonts:
Poppins
Karla

Please keep look and feel of new brand - example in the zip package I sent.

```html
<!DOCTYPE html>
<html lang="en">
<head>
<meta charset="utf-8">
<title>MRT Property Stationery</title>
<link href="https://fonts.googleapis.com/css2?family=Poppins:wght@400;500;600;700&family=Karla:wght@400;700&display=swap" rel="stylesheet">
<style>
:root{
  --navy:#000a20;
  --card-navy:#0b1120;
  --royal:#0056a2;
  --cyan:#00b5ef;
  --blue:#0088ce;
  --sky:#68cef2;
  --board:#b7b7b7;
  --paper:#ffffff;
  --ink:#1d1d1f;
  --field:#e0e0e0;
}
*{margin:0;padding:0;box-sizing:border-box}
html,body{width:1200px;height:627px;overflow:hidden;background:var(--board)}
body{position:relative;font-family:'Poppins',sans-serif;color:var(--ink)}
.piece{position:absolute;background:var(--paper);box-shadow:0 1px 4px rgba(0,0,0,.25)}
.wordmark{font-family:'Poppins',sans-serif;font-weight:700;color:var(--royal);letter-spacing:.5px;line-height:1;display:flex;align-items:center;gap:4px}
.wordmark .dot{display:inline-block;border-radius:50%;background:var(--blue)}
.ico{display:inline-block;width:3px;height:3px;border-radius:50%;background:var(--blue);margin-right:2px;vertical-align:middle}

/* dark business cards */
.card-dark{background:var(--card-navy);border-radius:8px}
.card-front{left:83px;top:105px;width:175px;height:100px}
.card-front .wordmark{position:absolute;left:16px;top:42px;font-size:18px}
.card-front .wordmark .dot{width:8px;height:8px}
.card-front .divider{position:absolute;left:93px;top:25px;width:1px;height:52px;background:var(--blue)}
.card-front .info{position:absolute;left:99px;top:24px;color:#fff;font-size:5px;line-height:1.35}
.card-front .name{color:var(--blue);font-weight:700;font-size:7px;line-height:1.1}
.card-front .info p+p{margin-top:2px}
.card-back{left:83px;top:240px;width:175px;height:100px;display:flex;align-items:center;justify-content:center}
.card-back .wordmark{font-size:36px;gap:8px}
.card-back .wordmark .dot{width:16px;height:16px}

/* letterhead */
.letterhead{left:327px;top:105px;width:190px;height:270px;font-size:3.4px;line-height:1.3;padding:0 9px}
.letterhead .wordmark{position:absolute;left:10px;top:21px;font-size:20px}
.letterhead .wordmark .dot{width:8px;height:8px}
.letterhead .head-rule{position:absolute;left:127px;top:14px;width:1px;height:24px;background:var(--blue)}
.letterhead .contact{position:absolute;left:137px;top:14px;font-size:3.3px;line-height:1.3}
.letterhead .body{position:absolute;left:9px;top:62px;right:9px}
.letterhead .body p{margin-bottom:4px}
.letterhead .salute{font-weight:600;font-size:4.5px}
.letterhead .signature{width:40px;height:10px;margin-top:16px;background:linear-gradient(90deg,#e9ecf1,#f6f7f9);border-radius:2px}

/* folder */
.folder-cover{left:573px;top:116px;width:212px;height:118px;display:flex;overflow:hidden}
.folder-cover .back{width:50%;background:var(--navy);position:relative}
.folder-cover .back .info{position:absolute;left:8px;bottom:8px;color:#fff;font-size:3.4px;line-height:1.4}
.folder-cover .front{width:50%;display:flex;align-items:center;justify-content:center}
.folder-cover .front .wordmark{font-size:17px}
.folder-cover .front .wordmark .dot{width:7px;height:7px}
.folder-inside{left:573px;top:244px;width:212px;height:128px;display:flex;overflow:hidden;background:#eeeeee}
.folder-inside .panel{width:50%;position:relative}
.folder-inside .panel.left{background:linear-gradient(90deg,#f7f7f7,#dcdcdc)}
.folder-inside .panel.right{background:#f2f2f2}
.folder-inside .pocket{position:absolute;left:0;right:0;bottom:0;height:40px}
.folder-inside .left .pocket{background:var(--sky);clip-path:polygon(0 30%,100% 0,100% 100%,0 100%)}
.folder-inside .right .pocket{background:var(--blue);clip-path:polygon(0 0,100% 30%,100% 100%,0 100%)}
.folder-inside .sheet{position:absolute;left:12px;top:10px;width:80px;height:100px;background:#fff;box-shadow:0 0 2px rgba(0,0,0,.2);padding:6px}
.folder-inside .sheet .wordmark{font-size:8px}
.folder-inside .sheet .wordmark .dot{width:4px;height:4px}
.folder-inside .sheet .line{height:1px;background:#cfcfcf;margin-top:3px}

/* white business card */
.card-light{left:73px;top:431px;width:234px;height:91px}
.card-light .wordmark{position:absolute;left:32px;top:36px;font-size:20px}
.card-light .wordmark .dot{width:9px;height:9px}
.card-light .divider{position:absolute;left:122px;top:16px;width:1px;height:60px;background:var(--blue)}
.card-light .info{position:absolute;left:131px;top:15px;font-size:6px;line-height:1.3;color:#333}
.card-light .name{color:var(--royal);font-weight:700;font-size:8.5px;line-height:1.15}
.card-light .info p+p{margin-top:3px}

/* envelopes */
.envelope-back{left:362px;top:436px;width:196px;height:86px}
.envelope-back .flap{position:absolute;left:0;right:0;top:0;height:26px;border-radius:0 0 16px 16px;box-shadow:0 1px 3px rgba(0,0,0,.18);display:flex;align-items:center;justify-content:center}
.envelope-back .wordmark{font-size:9px}
.envelope-front{left:602px;top:436px;width:195px;height:85px}
.envelope-front .wordmark{position:absolute;left:6px;top:12px;font-size:11px}
.envelope-front .wordmark .dot{width:5px;height:5px}
.envelope-front .addr{position:absolute;left:6px;top:32px;font-size:3px;line-height:1.3}

/* invoice */
.invoice{left:831px;top:103px;width:297px;height:420px;font-family:'Karla',sans-serif}
.invoice .wordmark{position:absolute;left:28px;top:30px;font-size:28px}
.invoice .wordmark .dot{width:12px;height:12px}
.invoice .title{position:absolute;right:27px;top:33px;font-family:'Poppins',sans-serif;font-size:13px;color:var(--blue);font-weight:500;letter-spacing:.5px}
.invoice .addr{position:absolute;left:28px;top:105px;font-size:5.2px;line-height:1.4}
.invoice .contact{position:absolute;left:120px;top:101px;font-size:5.2px;line-height:1.4}
.invoice .order{position:absolute;left:198px;top:97px;width:71px;height:30px;background:var(--blue);color:#fff;font-size:4.6px;line-height:1.6;padding:4px 5px}
.invoice .order span{display:inline-block;width:38px;border-bottom:.5px dotted #fff}
.invoice table{position:absolute;left:28px;top:160px;width:241px;border-collapse:collapse;font-size:5px}
.invoice th{height:13px;color:#fff;font-weight:500;font-family:'Poppins',sans-serif}
.invoice th.qty{background:var(--sky);width:44px}
.invoice th.desc{background:var(--blue);border-left:1px solid #fff;border-right:1px solid #fff}
.invoice th.amt{background:var(--cyan);width:44px}
.invoice td{height:12px;border:.6px solid #8a8a8a}
.invoice .totals{position:absolute;right:28px;top:308px;font-family:'Poppins',sans-serif;font-size:7.5px}
.invoice .totals div{display:flex;align-items:center;justify-content:flex-end;gap:5px;margin-bottom:3px}
.invoice .totals .box{width:44px;height:10px;background:var(--field)}
.invoice .totals .grand{margin-top:5px}
.invoice .totals .grand .box{height:15px;background:#fff;border:1px solid var(--blue)}
.invoice .note{position:absolute;left:28px;top:321px;border-left:3px solid var(--blue);padding-left:5px;font-size:4px;line-height:1.3;width:120px}
.invoice .sign{position:absolute;top:370px;width:70px;border-top:.6px solid var(--blue);font-size:4px;text-align:center;padding-top:3px}
.invoice .sign.recv{left:28px}
.invoice .sign.auth{left:123px}
</style>
</head>
<body>

<section class="piece card-dark card-front">
  <div class="wordmark"><span class="dot"></span>MRT</div>
  <div class="divider"></div>
  <div class="info">
    <p class="name">DANIEL REYES</p>
    <p>Managing Director</p>
    <p>Your address, City<br>State, Zip 1234</p>
    <p><span class="ico"></span>123 456 789<br><span class="ico"></span>info@yourmail.com<br><span class="ico"></span>www.yourwebsite.com</p>
  </div>
</section>

<section class="piece card-dark card-back">
  <div class="wordmark"><span class="dot"></span>MRT</div>
</section>

<section class="piece letterhead">
  <div class="wordmark"><span class="dot"></span>MRT</div>
  <div class="head-rule"></div>
  <div class="contact">
    <span class="ico"></span>123 456 789<br><span class="ico"></span>info@yourmail.com<br><span class="ico"></span>www.yourwebsite.com<br><br>Your address, City<br>State, Zip 1234
  </div>
  <div class="body">
    <p>January-03-2020</p>
    <p>Mr, Mark Ellis<br>President</p>
    <p>Harbor Corporation<br>123 Street Name, Suite# 10<br>City, State, 120023</p>
    <p class="salute">Dear Mr, Mark</p>
    <p>Lorem ipsum dolor sit amet, consectetur adipiscing elit, sed do eiusmod tempor incididunt ut labore et dolore magna aliqua. Ut enim ad minim veniam, quis nostrud exercitation ullamco laboris nisi ut aliquip ex ea commodo consequat.</p>
    <p>Duis aute irure dolor in reprehenderit in voluptate velit esse cillum dolore eu fugiat nulla pariatur. Ut enim ad minim veniam, quis nostrud exercitation ullamco laboris.</p>
    <p>Excepteur sint occaecat cupidatat non proident, sunt in culpa qui officia deserunt mollit anim id est laborum.</p>
    <p>Regards</p>
    <div class="signature" role="img" aria-label="Handwritten signature of Laura Hayes"></div>
  </div>
</section>

<section class="piece folder-cover">
  <div class="back">
    <div class="info">Your address, City State, Zip 1234<br>123 456 789 · info@yourmail.com · www.yourwebsite.com</div>
  </div>
  <div class="front"><div class="wordmark"><span class="dot"></span>MRT</div></div>
</section>

<section class="piece folder-inside">
  <div class="panel left"><div class="pocket"></div></div>
  <div class="panel right">
    <div class="sheet">
      <div class="wordmark"><span class="dot"></span>MRT</div>
      <div class="line"></div><div class="line"></div><div class="line"></div><div class="line"></div><div class="line"></div><div class="line"></div><div class="line"></div><div class="line"></div>
    </div>
    <div class="pocket"></div>
  </div>
</section>

<section class="piece card-light">
  <div class="wordmark"><span class="dot"></span>MRT</div>
  <div class="divider"></div>
  <div class="info">
    <p class="name">DANIEL REYES</p>
    <p>Managing Director</p>
    <p><span class="ico"></span>123 456 789<br><span class="ico"></span>info@yourmail.com<br><span class="ico"></span>www.yourwebsite.com</p>
    <p>Your address, City<br>State, Zip 1234</p>
  </div>
</section>

<section class="piece envelope-back">
  <div class="flap"><div class="wordmark">MRT</div></div>
</section>

<section class="piece envelope-front">
  <div class="wordmark"><span class="dot"></span>MRT</div>
  <div class="addr">Your address, City<br>State, Zip 1234</div>
</section>

<section class="piece invoice">
  <div class="wordmark"><span class="dot"></span>MRT</div>
  <div class="title">INVOICE</div>
  <div class="addr">Your address, City<br>State, Zip 1234</div>
  <div class="contact"><span class="ico"></span>123 456 789<br><span class="ico"></span>info@yourmail.com<br><span class="ico"></span>www.yourwebsite.com</div>
  <div class="order">Order No: <span></span><br>Page: <span></span><br>Date: <span></span></div>
  <table>
    <thead><tr><th class="qty">Quantity</th><th class="desc">Description</th><th class="amt">Amount</th></tr></thead>
    <tbody>
      <tr><td></td><td></td><td></td></tr><tr><td></td><td></td><td></td></tr>
      <tr><td></td><td></td><td></td></tr><tr><td></td><td></td><td></td></tr>
      <tr><td></td><td></td><td></td></tr><tr><td></td><td></td><td></td></tr>
      <tr><td></td><td></td><td></td></tr><tr><td></td><td></td><td></td></tr>
      <tr><td></td><td></td><td></td></tr><tr><td></td><td></td><td></td></tr>
      <tr><td></td><td></td><td></td></tr>
    </tbody>
  </table>
  <div class="note">All goods remain the property of northfieldworks.com until this Invoice is paid in full. Returns or claims accepted after 7 days.</div>
  <div class="totals">
    <div>Sub Total <span class="box"></span></div>
    <div>Tax <span class="box"></span></div>
    <div class="grand">Total <span class="box"></span></div>
  </div>
  <div class="sign recv">Received in good Condition</div>
  <div class="sign auth">Authorised Signature</div>
</section>

</body>
</html>
```